Stylish Business Cards Wanted

- DOUBLE SIDED Design Required -

High end, edgy cards for a corporate and personal stylist. Must include logo,
Name: Belinda Harwick
Title: Director and Stylist
telephone : +61 8 7142 5809
email: belinda@theloombriefing.example
website: theloombriefing.example
Tag: Corporate Workwear & Uniform Specialist | Personal Stylist
Would like nice icons for telephone, email, website

Target Market(s)

Businesses wanting stylish uniforms, people wanting stylish wardrobes

Industry/Entity Type

Corporate Workwear Stylist

Contact Information for Business Card

I would like black, white and gold foiling incorporated in the design - possibly a touch of the other colours on my branding guide attached Name: Belinda Harwick Title: Director and Stylist telephone : +61 8 7142 5809 email: belinda@theloombriefing.example website: theloombriefing.example Tag: Corporate Workwear & Uniform Specialist | Personal Stylist Would like nice icons for telephone, email, website

Font styles to use
Other font styles liked:
• Raleway

Colors

Designer to choose colors to be used in the design.

Requirements
Must have
• Gold foil accents

```html
<!DOCTYPE html>
<html lang="en">
<head>
<meta charset="utf-8">
<title>The Loom Briefing — Business Cards</title>
<link href="https://fonts.googleapis.com/css2?family=Raleway:wght@400;500;600&display=swap" rel="stylesheet">
<style>
  :root {
    --backdrop: #2b2b2c;
    --card-black: #1d1d1e;
    --card-white: #f4f4f6;
    --gold: #d3ae45;
    --gold-deep: #b98f2a;
    --magenta: #9e175c;
    --text-light: #c9c9cc;
    --text-muted: #a4a4a8;
  }
  * { box-sizing: border-box; margin: 0; padding: 0; }
  html, body {
    width: 1200px;
    height: 868px;
    overflow: hidden;
    background: var(--backdrop);
    font-family: "Raleway", sans-serif;
  }
  .canvas {
    position: relative;
    width: 1200px;
    height: 868px;
  }
  .card {
    position: absolute;
    border-radius: 3px;
    box-shadow: 0 18px 40px rgba(0,0,0,0.45);
  }
  .card--back {
    left: 150px;
    top: 164px;
    width: 340px;
    height: 540px;
    background: var(--card-black);
    border-bottom: 6px solid var(--magenta);
    border-left: 6px solid var(--magenta);
    display: flex;
    flex-direction: column;
    align-items: center;
    justify-content: center;
    text-align: center;
    color: var(--text-light);
  }
  .card--front {
    left: 560px;
    top: 269px;
    width: 530px;
    height: 330px;
    background: var(--card-white);
    border-bottom: 6px solid var(--magenta);
    border-left: 6px solid var(--magenta);
    display: flex;
    align-items: center;
    justify-content: center;
  }
  .person-name {
    color: var(--gold);
    font-weight: 600;
    font-size: 23px;
    letter-spacing: 0.06em;
    text-transform: uppercase;
  }
  .person-title {
    margin-top: 4px;
    font-size: 14px;
    font-weight: 400;
    color: var(--text-light);
  }
  .divider {
    width: 14px;
    height: 2px;
    background: var(--magenta);
    margin: 22px auto;
  }
  .contact-list {
    list-style: none;
    display: flex;
    flex-direction: column;
    align-items: center;
    gap: 6px;
    font-size: 13.5px;
  }
  .contact-list li {
    display: flex;
    align-items: center;
    gap: 7px;
  }
  .contact-icon {
    width: 12px;
    height: 12px;
    flex: none;
  }
  .services {
    list-style: none;
    font-size: 13px;
    letter-spacing: 0.06em;
    text-transform: uppercase;
    color: var(--text-muted);
    line-height: 1.45;
  }
  .brand {
    display: flex;
    align-items: center;
    gap: 14px;
    color: var(--gold);
    font-weight: 600;
    font-size: 30px;
    letter-spacing: 0.14em;
    text-transform: uppercase;
  }
  .brand-mark {
    width: 16px;
    height: 16px;
    background: var(--gold);
  }
</style>
</head>
<body>
<main class="canvas">

  <section class="card card--back" aria-label="Business card back">
    <h1 class="person-name">Belinda Harwick</h1>
    <p class="person-title">Director &amp; Stylist</p>
    <div class="divider"></div>
    <ul class="contact-list">
      <li>
        <svg class="contact-icon" viewBox="0 0 24 24" aria-hidden="true"><path fill="#d3ae45" d="M6.6 10.8a15.1 15.1 0 0 0 6.6 6.6l2.2-2.2c.3-.3.7-.4 1-.2 1.1.4 2.3.6 3.6.6.6 0 1 .4 1 1V20c0 .6-.4 1-1 1C10.6 21 3 13.4 3 4c0-.6.4-1 1-1h3.5c.6 0 1 .4 1 1 0 1.3.2 2.5.6 3.6.1.3 0 .7-.2 1z"/></svg>
        <span>+61 8 7142 5809</span>
      </li>
      <li>
        <svg class="contact-icon" viewBox="0 0 24 24" aria-hidden="true"><path fill="#d3ae45" d="M2 5h20v14H2z"/><path fill="none" stroke="#1d1d1e" stroke-width="1.8" d="M2.5 5.5 12 13l9.5-7.5"/></svg>
        <span>belinda@theloombriefing.example</span>
      </li>
      <li>
        <svg class="contact-icon" viewBox="0 0 24 24" aria-hidden="true"><circle cx="12" cy="12" r="10" fill="#d3ae45"/><path fill="none" stroke="#1d1d1e" stroke-width="1.6" d="M2 12h20M12 2c3 3 3 17 0 20M12 2c-3 3-3 17 0 20"/></svg>
        <span>theloombriefing.example</span>
      </li>
    </ul>
    <div class="divider"></div>
    <ul class="services">
      <li>Corporate Workwear</li>
      <li>Uniform Specialist</li>
      <li>Personal Stylist</li>
    </ul>
  </section>

  <section class="card card--front" aria-label="Business card front">
    <div class="brand">
      <span class="brand-mark" aria-hidden="true"></span>
      <span class="brand-name">The Loom Briefing</span>
    </div>
  </section>

</main>
</body>
</html>
```